Custom Manufacturing Company square space website design

I own a custom manufacturing company that uses precision cutting technology to manufacture project components over a couple industries. We have an industrial CNC router and state of the art edge bander and cut a lot of cabinetry components for cabinet shops, builders, closet companies, ect. We offer design and assembly for any cabinetry or can build cabinets to spec. We also cut components for other industries out of wood, plastics, acryclics, ect. We offer design engineering services, product development protype services. we have a 3D printer farm. We want our communicate trust, dependability, and the value we place on client relationships.

We essentially want a credibility website. Landing page and drops downs for services we offer, capabilites, about us, contact

```html
<!DOCTYPE html>
<html lang="en">
<head>
<meta charset="utf-8">
<title>North Loop CNC – Homepage Options</title>
<link href="https://fonts.googleapis.com/css2?family=Barlow:wght@400;500;600;700;800&family=Barlow+Condensed:wght@400;500&display=swap" rel="stylesheet">
<style>
:root{
  --ink:#141615;
  --dark:#1c1e1d;
  --panel:#191a19;
  --nav:#151716;
  --orange:#f07a1a;
  --green:#2c3a31;
  --card:#37473c;
  --grey:#3d403e;
  --line:#d9d9d9;
  --muted:#8a8d8b;
  --text:#5c5f5d;
  --white:#ffffff;
  --board:#ffffff;
}
*{box-sizing:border-box;margin:0;padding:0}
html,body{width:1200px;height:2358px;overflow:hidden;background:var(--board)}
body{font-family:"Barlow",Arial,sans-serif;color:var(--ink)}
.board{position:absolute;left:0;top:0;width:1310px;height:2574px;transform:scale(.91603);transform-origin:0 0}
.option-title{position:absolute;top:50px;width:501px;text-align:center;font-family:"Barlow Condensed",Arial,sans-serif;font-weight:400;font-size:40px;letter-spacing:1.5px;color:#111}
.page{position:absolute;top:117px;width:501px;height:2341px;background:var(--white);overflow:hidden;box-shadow:0 0 14px rgba(0,0,0,.12)}
.page *{position:absolute}
.page .flow,.page .flow *{position:static}
.photo{display:block}

/* hero */
.hero{left:0;top:0;width:501px;height:334px}
.opt1 .hero{background:linear-gradient(120deg,#5a4536 0%,#3b2c22 45%,#6e5846 70%,#2d241d 100%)}
.opt1 .hero::after{content:"";position:absolute;inset:0;background:rgba(20,16,12,.45)}
.opt2 .hero{background:radial-gradient(circle at 66% 58%,#f0b24a 0%,#a7651e 22%,#4a2e14 48%,#17120e 80%)}
.topbar-social{left:27px;top:3px;display:flex;gap:6px}
.dot-icon{position:static;display:block;width:6px;height:6px;border-radius:50%;background:#fff}
.phone{top:3px;right:27px;font-size:6px;color:#fff;display:flex;align-items:center;gap:3px}
.phone i{position:static;display:block;width:7px;height:7px;border-radius:50%;border:1px solid var(--orange)}
.opt2 .phone{top:3px;right:27px}
.navbar{left:27px;top:16px;width:447px;height:34px;background:var(--nav)}
.opt2 .navbar{left:28px;top:4px;width:446px;background:transparent;height:40px}
.brand{left:5px;top:3px;display:flex;flex-direction:column;align-items:center;gap:2px}
.brand .mark{position:static;width:18px;height:14px;border:1.2px solid #fff}
.brand .name{position:static;font-size:6.5px;font-weight:600;letter-spacing:1px;color:#fff;white-space:nowrap}
.opt2 .brand{left:0;top:2px}
.opt2 .brand .mark{width:26px;height:18px}
.opt2 .brand .name{font-size:7.5px}
.nav-links{right:10px;top:13px;display:flex;gap:14px;font-size:5.5px;font-weight:500;color:#fff}
.nav-links span{position:static}
.nav-links .active{color:var(--orange)}
.opt2 .nav-links{right:44px;top:28px}
.nav-social{display:none}
.opt2 .nav-social{display:flex;right:0;top:29px;gap:5px}

.hero-copy{left:0;top:113px;width:501px;text-align:center;color:#fff}
.hero-copy .eyebrow{position:static;display:block;font-size:11px;font-weight:500;letter-spacing:.4px}
.hero-copy h1{position:static;display:block;font-size:25px;font-weight:800;margin-top:4px;letter-spacing:.2px}
.hero-copy p{position:static;display:block;font-size:6.8px;margin-top:8px}
.btn-light{left:219px;top:204px;width:62px;height:20px;background:#fff;color:#111;font-size:5.5px;font-weight:700;display:flex;align-items:center;justify-content:center}
.opt2 .hero-copy{left:28px;top:98px;width:240px;text-align:left}
.opt2 .hero-copy .eyebrow{font-size:12px;font-weight:600}
.opt2 .hero-copy h1{font-size:24px;line-height:30px;margin-top:2px}
.opt2 .hero-copy h1 em{font-style:normal;color:var(--orange)}
.opt2 .hero-copy p{font-size:7px;line-height:12px;margin-top:6px;width:180px}
.opt2 .btn-light{left:28px;top:218px}

/* capability panel */
.hero-fade{left:0;top:278px;width:27px;height:124px;background:#c7c7c7;clip-path:polygon(0 0,100% 2%,100% 92%,0 100%)}
.cap-panel{left:27px;top:281px;width:447px;height:267px;background:var(--panel);clip-path:polygon(0 0,100% 0,100% 100%,0 55.8%)}
.opt2 .cap-panel{top:313px;height:235px;clip-path:polygon(0 0,100% 0,100% 100%,0 49.8%)}
.cap-intro{left:42px;top:333px;color:#fff}
.cap-intro small{position:static;display:block;font-size:6px}
.cap-intro h2{position:static;display:block;font-size:19px;line-height:25px;font-weight:800;margin-top:4px}
.cap-item{width:100px;color:#fff}
.cap-item svg{position:static;display:block;width:24px;height:24px}
.cap-item h3{position:static;display:block;font-size:7.5px;font-weight:500;margin-top:9px}
.cap-item p{position:static;display:block;font-size:5.3px;line-height:9px;color:#b9bbba;margin-top:6px}
.cap-cabinet{left:176px;top:335px}
.cap-builders{left:371px;top:335px}
.cap-closet{left:273px;top:410px}

/* shared section type */
.eyebrow-dark{font-size:6.2px;font-weight:500;color:#222;letter-spacing:.2px}
.h2{font-size:18px;font-weight:800;color:#111;letter-spacing:.1px}
.h2 em{font-style:normal;color:var(--orange)}
.body{font-size:5.6px;line-height:10.8px;color:var(--text)}
.btn-dark{width:60px;height:20px;background:var(--ink);color:#fff;font-size:5px;font-weight:700;display:flex;align-items:center;justify-content:center;box-shadow:2px 2px 0 #bdbdbd}
.frame{border-top:1px solid var(--orange);border-left:1px solid var(--orange);height:14px}
.frame::after{content:"";position:absolute;right:-2px;top:-2px;width:3px;height:3px;border-radius:50%;background:var(--ink)}
.opt2 .frame{display:none}

/* welcome */
.welcome-photo{left:27px;top:524px;width:200px;height:208px;background:linear-gradient(135deg,#8a7868,#3d4a5e 45%,#2a3442 70%,#8f8170)}
.welcome-frame{left:251px;top:548px;width:151px}
.welcome-eyebrow{left:256px;top:554px}
.welcome-title{left:256px;top:567px}
.welcome-text{left:256px;top:598px;width:220px}
.welcome-btn{left:256px;top:679px}

/* services */
.services{left:0;top:771px;width:501px;height:297px;background:linear-gradient(180deg,#26322b,#2f3d34)}
.services-frame{left:184px;top:798px;width:141px;border-color:#c9c9c9}
.services-frame::after{background:#fff}
.services-eyebrow{left:0;top:803px;width:501px;text-align:center;font-size:6px;color:#cfd3d0}
.services-title{left:0;top:815px;width:501px;text-align:center;color:#fff}
.services-sub{left:0;top:843px;width:501px;text-align:center;font-size:6px;color:#98a29b}
.service-card{top:870px;width:142px;height:165px;background:var(--card)}
.service-card .photo{position:absolute;left:13px;top:13px;width:116px;height:112px;clip-path:polygon(0 0,100% 0,84% 100%,16% 100%)}
.service-card h3{left:0;top:134px;width:142px;text-align:center;font-size:7px;font-weight:600;color:#fff}
.service-card p{left:0;top:146px;width:142px;text-align:center;font-size:5px;color:#aab3ad}
.svc-1{left:27px}.svc-2{left:180px}.svc-3{left:332px}
.svc-1 .photo{background:linear-gradient(160deg,#c97a2a,#5a6068 50%,#2c3238)}
.svc-2 .photo{background:linear-gradient(180deg,#3a3a3a,#b5705a 55%,#e0b39a)}
.svc-3 .photo{background:linear-gradient(160deg,#1e2c3c,#2a8fb0 45%,#e07a2a 80%,#3a2a22)}

/* products */
.products-frame{left:24px;top:1106px;width:144px}
.products-eyebrow{left:28px;top:1112px}
.products-title{left:28px;top:1125px}
.products-sub{left:28px;top:1153px;font-size:5.6px;color:var(--text)}
.material{left:28px;width:173px;font-size:6.2px;color:#333;padding-bottom:7px}
.material.active{font-weight:700;color:#111;border-bottom:1px solid #e2e2e2}
.mat-wood{top:1188px}.mat-plastics{top:1213px}.mat-acrylics{top:1238px}
.product{width:80px}
.product .photo{position:absolute;left:0;top:0;width:80px;height:102px}
.product h4{top:107px;left:0;font-size:6px;font-weight:600;color:#222;white-space:nowrap}
.product span{top:119px;left:0;font-size:3.8px;color:var(--orange)}
.prod-1{left:223px;top:1107px}.prod-2{left:308px;top:1137px}.prod-3{left:394px;top:1167px}
.prod-1 .photo{background:linear-gradient(150deg,#e3d3ae,#c9b48a 60%,#a89371)}
.prod-2 .photo{background:linear-gradient(150deg,#9a9a96,#e6dfcf 40%,#cfc6b4)}
.prod-3 .photo{background:linear-gradient(150deg,#d9d2c4,#efe9dd 50%,#b9b2a4)}

/* blog */
.blog{left:0;top:1330px;width:501px;height:278px;background:var(--dark)}
.blog-frame{left:189px;top:1355px;width:132px;border-color:var(--orange)}
.blog-frame::after{background:#fff}
.blog-eyebrow{left:0;top:1361px;width:501px;text-align:center;font-size:6px;color:#cfd0cf}
.blog-title{left:0;top:1374px;width:501px;text-align:center;color:#fff}
.post{top:1410px;width:144px}
.post .photo{position:absolute;left:0;top:0;width:144px;height:88px}
.post time{top:99px;left:0;font-size:4.2px;color:#c9c9c9;white-space:nowrap}
.post time b{position:static;font-weight:400;color:var(--orange)}
.post h4{top:112px;left:0;width:144px;font-size:7.2px;line-height:11px;font-weight:500;color:#fff}
.post .btn-post{top:146px;left:1px;width:62px;height:18px;background:var(--grey);color:#fff;font-size:4.8px;font-weight:700;display:flex;align-items:center;justify-content:center}
.post-1{left:27px}.post-2{left:179px}.post-3{left:330px}
.post-1 .photo{background:linear-gradient(120deg,#b58a5a,#6b4b30 45%,#2e4966)}
.post-2 .photo{background:linear-gradient(120deg,#5b5244,#b2946a 45%,#3b3a36)}
.post-3 .photo{background:linear-gradient(120deg,#5a3a1c,#f0a83a 50%,#7a5030)}

/* printer farm */
.farm-frame{left:23px;top:1674px;width:160px}
.farm-eyebrow{left:28px;top:1680px}
.farm-title{left:28px;top:1692px}
.farm-text{left:28px;top:1724px;width:220px}
.farm-btn{left:28px;top:1804px}
.farm-photo{left:275px;top:1650px;width:199px;height:207px;background:radial-gradient(circle at 50% 72%,#3a4cff 0%,#1a2570 25%,#141a2c 55%,#0d0f14 100%)}

/* contact */
.contact{left:0;top:1898px;width:501px;height:252px;background:var(--dark)}
.map{left:418px;top:1898px;width:83px;height:252px;background:linear-gradient(160deg,#5d6a5f,#4d5a50 50%,#566358)}
.contact-title{left:28px;top:1934px;color:#fff}
.contact-underline{left:28px;top:1958px;width:115px;height:1px;background:var(--orange)}
.contact-row{left:31px;display:flex;gap:8px;align-items:flex-start;color:#d7d7d7;font-size:5.6px;line-height:9.5px}
.contact-row i{position:static;display:block;flex:none;width:9px;height:9px;border-radius:50%;background:#3a3b3a;border:1px solid var(--orange)}
.contact-row span{position:static}
.row-address{top:1977px}.row-phone{top:2014px}.row-email{top:2042px}
.contact-divider{left:28px;width:140px;height:1px;background:#2b2d2c}
.follow{left:28px;top:2091px;font-size:7px;font-weight:600;color:#fff}
.follow-icons{left:28px;top:2110px;display:flex;gap:6px}
.form-title{left:181px;top:1945px;font-size:8.5px;color:#fff}
.form-sub{left:181px;top:1961px;font-size:4.6px;color:#a6a6a6}
.field{left:181px;width:171px;font-size:5px;color:#d0d0d0;border-bottom:1px solid #8c8c8c}
.f-name{top:1986px;height:15px}.f-email{top:2012px;height:16px}.f-message{top:2039px;height:26px}
.submit{left:181px;top:2071px;width:171px;height:21px;background:#454746;color:#fff;font-size:5.5px;font-weight:600;display:flex;align-items:center;justify-content:center}

/* footer */
.footer{left:0;top:2150px;width:501px;height:191px;background:#000}
.opt2 .footer{background:#fff}
.footer-brand{left:27px;top:2186px;width:220px;height:120px;border:1px solid #444;display:flex;flex-direction:column;align-items:center;justify-content:center;gap:10px}
.opt2 .footer-brand{border-color:#dcdcdc}
.footer-brand .mark{position:static;width:60px;height:42px;border:2px solid #fff}
.footer-brand .name{position:static;font-size:15px;font-weight:600;letter-spacing:3px;color:#fff;white-space:nowrap}
.opt2 .footer-brand .mark{border-color:#111}
.opt2 .footer-brand .name{color:#111}
.footer-rule{left:247px;top:2186px;width:141px;height:1px;background:#444}
.opt2 .footer-rule{background:#dcdcdc}
.links{top:2203px}
.links h5{position:static;display:block;font-size:6.5px;font-weight:600;color:#fff;margin-bottom:4px}
.links .tick{position:static;display:block;width:10px;height:1px;background:var(--orange);margin-bottom:6px}
.links a{position:static;display:block;font-size:5px;color:#cfcfcf;line-height:14px;text-decoration:none}
.opt2 .links h5{color:#111}
.opt2 .links a{color:#555}
.links-quick{left:247px}.links-other{left:389px}
.copyright{left:27px;top:2320px;font-size:4.5px;color:#bdbdbd}
.copyright b{position:static;color:#fff}
.opt2 .copyright{color:#555}
.opt2 .copyright b{color:#111}
.opt2 .follow-icons .dot-icon,.follow-icons .dot-icon{background:#fff}
</style>
</head>
<body>
<div class="board">

  <div class="option-title" style="left:101px">OPTION 1</div>
  <div class="option-title" style="left:708px">OPTION 2</div>

  <!-- ============ Option 1 ============ -->
  <section class="page opt1" style="left:101px">
    <div class="hero photo" role="img" aria-label="Craftsman working wood at a bench in a brick workshop"></div>
    <div class="topbar-social"><i class="dot-icon"></i><i class="dot-icon"></i><i class="dot-icon"></i></div>
    <div class="phone"><i></i>+1 555-014-2290</div>
    <nav class="navbar">
      <div class="brand"><i class="mark"></i><b class="name">NORTH LOOP CNC</b></div>
      <div class="nav-links"><span class="active">HOME</span><span>ABOUT US</span><span>SERVICE</span><span>BLOG</span><span>CONTACT US</span></div>
    </nav>
    <div class="hero-copy">
      <span class="eyebrow">INDUSTRIAL CNC ROUTER</span>
      <h1>PRECISION CUTTING TECHNOLOGY</h1>
      <p>We offer design and assembly for any cabinetry or can build cabinets to spec</p>
    </div>
    <div class="btn-light">GET STARTED</div>

    <div class="hero-fade"></div>
    <div class="cap-panel"></div>
    <div class="cap-intro"><small>WE HAVE AN</small><h2>INDUSTRIAL<br>CNC ROUTER</h2></div>
    <div class="cap-item cap-cabinet">
      <svg viewBox="0 0 24 24" fill="none" stroke="#fff" stroke-width="1.3"><rect x="3" y="3" width="18" height="18" rx="1"/><line x1="3" y1="9" x2="21" y2="9"/><line x1="3" y1="15" x2="21" y2="15"/><line x1="10" y1="6" x2="14" y2="6"/><line x1="10" y1="12" x2="14" y2="12"/><line x1="10" y1="18" x2="14" y2="18"/></svg>
      <h3>Cabinet Shops</h3><p>Excepteur sint occaecat cupidatat non proident, sunt in culpa</p>
    </div>
    <div class="cap-item cap-builders">
      <svg viewBox="0 0 24 24" fill="none" stroke="#fff" stroke-width="1.3"><rect x="2" y="8" width="16" height="13" rx="1"/><line x1="2" y1="14" x2="18" y2="14"/><line x1="8" y1="11" x2="12" y2="11"/><circle cx="18" cy="6" r="4"/><polyline points="16,6 17.5,7.5 20,4.5"/></svg>
      <h3>Builders</h3><p>Excepteur sint occaecat cupidatat non proident, sunt in culpa</p>
    </div>
    <div class="cap-item cap-closet">
      <svg viewBox="0 0 24 24" fill="none" stroke="#fff" stroke-width="1.3"><rect x="2" y="4" width="20" height="15" rx="1"/><line x1="12" y1="4" x2="12" y2="19"/><line x1="5" y1="21" x2="5" y2="19"/><line x1="19" y1="21" x2="19" y2="19"/><line x1="10" y1="11" x2="14" y2="11"/></svg>
      <h3>Closet Companies</h3><p>Excepteur sint occaecat cupidatat non proident, sunt in culpa</p>
    </div>

    <div class="welcome-photo photo" role="img" aria-label="Technician in ear protection operating a router"></div>
    <div class="frame welcome-frame"></div>
    <div class="eyebrow-dark welcome-eyebrow">WELCOME TO</div>
    <h2 class="h2 welcome-title">NORTH LOOP <em>CNC</em></h2>
    <p class="body welcome-text">Sed ut perspiciatis unde omnis iste natus error sit voluptatem accusantium doloremque laudantium, totam rem aperiam, eaque ipsa quae ab illo inventore veritatis et quasi architecto beatae vitae dicta sunt explicabo. Nemo enim ipsam voluptatem quia voluptas sit aspernatur aut odit aut fugit, sed quia consequuntur magni dolores eos qui ratione voluptatem sequi nesciunt.</p>
    <div class="btn-dark welcome-btn">READ MORE</div>

    <div class="services"></div>
    <div class="frame services-frame"></div>
    <div class="services-eyebrow">WHAT WE OFFER</div>
    <h2 class="h2 services-title">OUR SERVICES</h2>
    <div class="services-sub">Duis aute irure dolor in reprehenderit in voluptate velit esse cillum dolore</div>
    <article class="service-card svc-1"><div class="photo" role="img" aria-label="Engineer in hard hat at a machine"></div><h3>ENGINEERING SERVICES</h3><p>Duis aute irure dolor in reprehenderit...</p></article>
    <article class="service-card svc-2"><div class="photo" role="img" aria-label="CNC spindle carving a pattern"></div><h3>PRODUCT DEVELOPMENT</h3><p>Duis aute irure dolor in reprehenderit...</p></article>
    <article class="service-card svc-3"><div class="photo" role="img" aria-label="Machine cutting metal with sparks"></div><h3>PROTYPE SERVICES</h3><p>Duis aute irure dolor in reprehenderit...</p></article>

    <div class="frame products-frame"></div>
    <div class="eyebrow-dark products-eyebrow">WHAT WE DO</div>
    <h2 class="h2 products-title">OUR PRODUCTS</h2>
    <div class="products-sub">Duis aute irure dolor in reprehenderit in voluptate velit esse...</div>
    <div class="material active mat-wood">WOOD</div>
    <div class="material mat-plastics">PLASTICS</div>
    <div class="material mat-acrylics">ACRYCLICS</div>
    <div class="product prod-1"><div class="photo" role="img" aria-label="Raised cabinet door panels"></div><h4>Dolor Repellendus</h4><span>View Details</span></div>
    <div class="product prod-2"><div class="photo" role="img" aria-label="Shaker style cabinet door"></div><h4>Dolor Repellendus</h4><span>View Details</span></div>
    <div class="product prod-3"><div class="photo" role="img" aria-label="Grooved panel door"></div><h4>Dolor Repellendus</h4><span>View Details</span></div>

    <div class="blog"></div>
    <div class="frame blog-frame"></div>
    <div class="blog-eyebrow">NEWS &amp; ARTICLE</div>
    <h2 class="h2 blog-title">RECENT BLOG</h2>
    <article class="post post-1"><div class="photo" role="img" aria-label="Saw cutting a board"></div><time>22TH AUGUST, <b>2023</b></time><h4>Consequences that are extremely painful pursues</h4><div class="btn-post">READ MORE</div></article>
    <article class="post post-2"><div class="photo" role="img" aria-label="Worker at a metal lathe"></div><time>22TH AUGUST, <b>2023</b></time><h4>Consequences that are extremely painful pursues</h4><div class="btn-post">READ MORE</div></article>
    <article class="post post-3"><div class="photo" role="img" aria-label="Angle grinder throwing sparks"></div><time>22TH AUGUST, <b>2023</b></time><h4>Consequences that are extremely painful pursues</h4><div class="btn-post">READ MORE</div></article>

    <div class="frame farm-frame"></div>
    <div class="eyebrow-dark farm-eyebrow">WE HAVE A</div>
    <h2 class="h2 farm-title">3D PRINTER FARM</h2>
    <p class="body farm-text">Sed ut perspiciatis unde omnis iste natus error sit voluptatem accusantium doloremque laudantium, totam rem aperiam, eaque ipsa quae ab illo inventore veritatis et quasi architecto beatae vitae dicta sunt explicabo. Nemo enim ipsam voluptatem quia voluptas sit aspernatur aut odit aut fugit, sed quia consequuntur magni dolores eos qui ratione voluptatem sequi nesciunt.</p>
    <div class="btn-dark farm-btn">READ MORE</div>
    <div class="farm-photo photo" role="img" aria-label="3D printer head with glowing blue print"></div>

    <div class="contact"></div>
    <div class="map photo" role="img" aria-label="Street map of the shop location"></div>
    <h2 class="h2 contact-title">CONTACT US</h2>
    <div class="contact-underline"></div>
    <div class="contact-row row-address"><i></i><span>220 Alder Ave NE, Ferndale,<br>MN 55000</span></div>
    <div class="contact-divider" style="top:2004px"></div>
    <div class="contact-row row-phone"><i></i><span>+1 555-014-2290</span></div>
    <div class="contact-divider" style="top:2031px"></div>
    <div class="contact-row row-email"><i></i><span>hello@northloopcnc.com</span></div>
    <div class="contact-divider" style="top:2075px"></div>
    <div class="follow">FOLLOW US</div>
    <div class="follow-icons"><i class="dot-icon"></i><i class="dot-icon"></i><i class="dot-icon"></i></div>
    <div class="form-title">You Have Any Question</div>
    <div class="form-sub">Nor again is there anyone who loves or pursues or desires</div>
    <div class="field f-name">Name:</div>
    <div class="field f-email">Email:</div>
    <div class="field f-message">Message:</div>
    <div class="submit">SUBMIT</div>

    <footer class="footer"></footer>
    <div class="footer-brand"><i class="mark"></i><b class="name">NORTH LOOP CNC</b></div>
    <div class="footer-rule"></div>
    <div class="links links-quick"><h5>QUICK LINKS</h5><i class="tick"></i><a>Home</a><a>About Us</a><a>Services</a><a>Blog</a><a>Contact Us</a></div>
    <div class="links links-other"><h5>OTHERS LINK</h5><i class="tick"></i><a>Privacy Policy</a><a>Terms &amp; Condition</a><a>Cookies Policy</a><a>Help!</a></div>
    <div class="copyright">COPYRIGHT © 2023 <b>NORTH LOOP CNC</b>. ALL RIGHTS RESERVED.</div>
  </section>

  <!-- ============ Option 2 ============ -->
  <section class="page opt2" style="left:708px">
    <div class="hero photo" role="img" aria-label="CNC spindle cutting an ornate brass part with sparks"></div>
    <div class="phone"><i></i>+1 555-014-2290</div>
    <nav class="navbar">
      <div class="brand"><i class="mark"></i><b class="name">NORTH LOOP CNC</b></div>
      <div class="nav-links"><span class="active">HOME</span><span>ABOUT US</span><span>SERVICE</span><span>BLOG</span><span>CONTACT US</span></div>
      <div class="nav-social"><i class="dot-icon"></i><i class="dot-icon"></i><i class="dot-icon"></i></div>
    </nav>
    <div class="hero-copy">
      <span class="eyebrow">PRECISION</span>
      <h1><em>CUTTING</em><br>TECHNOLOGY</h1>
      <p>We offer design and assembly for any cabinetry or can build cabinets to spec</p>
    </div>
    <div class="btn-light">GET STARTED</div>

    <div class="cap-panel"></div>
    <div class="cap-intro"><small>WE HAVE AN</small><h2>INDUSTRIAL<br>CNC ROUTER</h2></div>
    <div class="cap-item cap-cabinet">
      <svg viewBox="0 0 24 24" fill="none" stroke="#fff" stroke-width="1.3"><rect x="3" y="3" width="18" height="18" rx="1"/><line x1="3" y1="9" x2="21" y2="9"/><line x1="3" y1="15" x2="21" y2="15"/><line x1="10" y1="6" x2="14" y2="6"/><line x1="10" y1="12" x2="14" y2="12"/><line x1="10" y1="18" x2="14" y2="18"/></svg>
      <h3>Cabinet Shops</h3><p>Excepteur sint occaecat cupidatat non proident, sunt in culpa</p>
    </div>
    <div class="cap-item cap-builders">
      <svg viewBox="0 0 24 24" fill="none" stroke="#fff" stroke-width="1.3"><rect x="2" y="8" width="16" height="13" rx="1"/><line x1="2" y1="14" x2="18" y2="14"/><line x1="8" y1="11" x2="12" y2="11"/><circle cx="18" cy="6" r="4"/><polyline points="16,6 17.5,7.5 20,4.5"/></svg>
      <h3>Builders</h3><p>Excepteur sint occaecat cupidatat non proident, sunt in culpa</p>
    </div>
    <div class="cap-item cap-closet">
      <svg viewBox="0 0 24 24" fill="none" stroke="#fff" stroke-width="1.3"><rect x="2" y="4" width="20" height="15" rx="1"/><line x1="12" y1="4" x2="12" y2="19"/><line x1="5" y1="21" x2="5" y2="19"/><line x1="19" y1="21" x2="19" y2="19"/><line x1="10" y1="11" x2="14" y2="11"/></svg>
      <h3>Closet Companies</h3><p>Excepteur sint occaecat cupidatat non proident, sunt in culpa</p>
    </div>

    <div class="welcome-photo photo" role="img" aria-label="Technician in ear protection operating a router"></div>
    <div class="eyebrow-dark welcome-eyebrow">WELCOME TO</div>
    <h2 class="h2 welcome-title">NORTH LOOP <em>CNC</em></h2>
    <p class="body welcome-text">Sed ut perspiciatis unde omnis iste natus error sit voluptatem accusantium doloremque laudantium, totam rem aperiam, eaque ipsa quae ab illo inventore veritatis et quasi architecto beatae vitae dicta sunt explicabo. Nemo enim ipsam voluptatem quia voluptas sit aspernatur aut odit aut fugit, sed quia consequuntur magni dolores eos qui ratione voluptatem sequi nesciunt.</p>
    <div class="btn-dark welcome-btn">READ MORE</div>

    <div class="services"></div>
    <div class="services-eyebrow">WHAT WE OFFER</div>
    <h2 class="h2 services-title">OUR SERVICES</h2>
    <div class="services-sub">Duis aute irure dolor in reprehenderit in voluptate velit esse cillum dolore</div>
    <article class="service-card svc-1"><div class="photo" role="img" aria-label="Engineer in hard hat at a machine"></div><h3>ENGINEERING SERVICES</h3><p>Duis aute irure dolor in reprehenderit...</p></article>
    <article class="service-card svc-2"><div class="photo" role="img" aria-label="CNC spindle carving a pattern"></div><h3>PRODUCT DEVELOPMENT</h3><p>Duis aute irure dolor in reprehenderit...</p></article>
    <article class="service-card svc-3"><div class="photo" role="img" aria-label="Machine cutting metal with sparks"></div><h3>PROTYPE SERVICES</h3><p>Duis aute irure dolor in reprehenderit...</p></article>

    <div class="eyebrow-dark products-eyebrow">WHAT WE DO</div>
    <h2 class="h2 products-title">OUR PRODUCTS</h2>
    <div class="products-sub">Duis aute irure dolor in reprehenderit in voluptate velit esse...</div>
    <div class="material active mat-wood">WOOD</div>
    <div class="material mat-plastics">PLASTICS</div>
    <div class="material mat-acrylics">ACRYCLICS</div>
    <div class="product prod-1"><div class="photo" role="img" aria-label="Raised cabinet door panels"></div><h4>Dolor Repellendus</h4><span>View Details</span></div>
    <div class="product prod-2"><div class="photo" role="img" aria-label="Shaker style cabinet door"></div><h4>Dolor Repellendus</h4><span>View Details</span></div>
    <div class="product prod-3"><div class="photo" role="img" aria-label="Grooved panel door"></div><h4>Dolor Repellendus</h4><span>View Details</span></div>

    <div class="blog"></div>
    <div class="blog-eyebrow">NEWS &amp; ARTICLE</div>
    <h2 class="h2 blog-title">RECENT BLOG</h2>
    <article class="post post-1"><div class="photo" role="img" aria-label="Saw cutting a board"></div><time>22TH AUGUST, <b>2023</b></time><h4>Consequences that are extremely painful pursues</h4><div class="btn-post">READ MORE</div></article>
    <article class="post post-2"><div class="photo" role="img" aria-label="Worker at a metal lathe"></div><time>22TH AUGUST, <b>2023</b></time><h4>Consequences that are extremely painful pursues</h4><div class="btn-post">READ MORE</div></article>
    <article class="post post-3"><div class="photo" role="img" aria-label="Angle grinder throwing sparks"></div><time>22TH AUGUST, <b>2023</b></time><h4>Consequences that are extremely painful pursues</h4><div class="btn-post">READ MORE</div></article>

    <div class="eyebrow-dark farm-eyebrow">WE HAVE A</div>
    <h2 class="h2 farm-title">3D PRINTER FARM</h2>
    <p class="body farm-text">Sed ut perspiciatis unde omnis iste natus error sit voluptatem accusantium doloremque laudantium, totam rem aperiam, eaque ipsa quae ab illo inventore veritatis et quasi architecto beatae vitae dicta sunt explicabo. Nemo enim ipsam voluptatem quia voluptas sit aspernatur aut odit aut fugit, sed quia consequuntur magni dolores eos qui ratione voluptatem sequi nesciunt.</p>
    <div class="btn-dark farm-btn">READ MORE</div>
    <div class="farm-photo photo" role="img" aria-label="3D printer head with glowing blue print"></div>

    <div class="contact"></div>
    <div class="map photo" role="img" aria-label="Street map of the shop location"></div>
    <h2 class="h2 contact-title">CONTACT US</h2>
    <div class="contact-row row-address"><i></i><span>220 Alder Ave NE, Ferndale,<br>MN 55000</span></div>
    <div class="contact-divider" style="top:2004px"></div>
    <div class="contact-row row-phone"><i></i><span>+1 555-014-2290</span></div>
    <div class="contact-divider" style="top:2031px"></div>
    <div class="contact-row row-email"><i></i><span>hello@northloopcnc.com</span></div>
    <div class="contact-divider" style="top:2075px"></div>
    <div class="follow">FOLLOW US</div>
    <div class="follow-icons"><i class="dot-icon"></i><i class="dot-icon"></i><i class="dot-icon"></i></div>
    <div class="form-title">You Have Any Question</div>
    <div class="form-sub">Nor again is there anyone who loves or pursues or desires</div>
    <div class="field f-name">Name:</div>
    <div class="field f-email">Email:</div>
    <div class="field f-message">Message:</div>
    <div class="submit">SUBMIT</div>

    <footer class="footer"></footer>
    <div class="footer-brand"><i class="mark"></i><b class="name">NORTH LOOP CNC</b></div>
    <div class="footer-rule"></div>
    <div class="links links-quick"><h5>QUICK LINKS</h5><i class="tick"></i><a>Home</a><a>About Us</a><a>Services</a><a>Blog</a><a>Contact Us</a></div>
    <div class="links links-other"><h5>OTHERS LINK</h5><i class="tick"></i><a>Privacy Policy</a><a>Terms &amp; Condition</a><a>Cookies Policy</a><a>Help!</a></div>
    <div class="copyright">COPYRIGHT © 2023 <b>NORTH LOOP CNC</b>. ALL RIGHTS RESERVED.</div>
  </section>

</div>
</body>
</html>
```